Website for software company "velora"

We need a website for our software company/startup named "velora". We are developing several products (currently 3 standard-software products) which are all in different sectors, but all our products are available for Laptops/PC/Mobile Phones/Tablets, ... We do also create custom software and support our customers with consulting to optimize their processes.
We already have a Logo which you can find in the attached files.
We are a young team of 4 members (two founders and 2 employees).

To get an idea of our products -> the first one is a planning software for healthcare organizations (eg. BlueHaven, firebrigade, pharmacy), the second one is a booking software for sport clubs and the third one is a competition software for sports hunting. You see very diverse. Include or ignore this info of our products as you like.

The design has to be a bootstrap 4 (or higher) design. We have licenced FontAwesome as iconset. Responsive design should come without saying.

• Starting page, product pages, news section, contact, team, services

```html
<!DOCTYPE html>
<html lang="en">
<head>
<meta charset="utf-8">
<title>velora — Software</title>
<link href="https://fonts.googleapis.com/css2?family=Nunito:wght@400;600;700;800&display=swap" rel="stylesheet">
<style>
:root{
  --orange:#f47920;
  --navy:#262e3b;
  --navy-deep:#1f2530;
  --card:#2f3848;
  --ink:#2a2f38;
  --muted:#555c66;
  --white:#ffffff;
  --line:#e3e5e8;
}
*{box-sizing:border-box;margin:0;padding:0}
html,body{width:1200px;height:3748px;overflow:hidden}
body{font-family:"Nunito",Arial,sans-serif;color:var(--ink);background:var(--white);position:relative}
.btn{position:absolute;background:var(--orange);color:var(--white);font-size:12px;font-weight:600;text-transform:uppercase;display:flex;align-items:center;justify-content:center;letter-spacing:.2px}
.accent{color:var(--orange)}

/* top bar */
.topbar{position:absolute;left:0;top:0;width:1200px;height:20px;background:var(--navy-deep);color:var(--white);font-size:11px}
.topbar .soc{position:absolute;top:6px;width:8px;height:8px;background:#c9ccd2;border-radius:1px}
.topbar-contact{position:absolute;right:129px;top:3px;display:flex;gap:16px;align-items:center;line-height:14px}
.topbar-contact span{display:flex;align-items:center;gap:4px}

/* nav */
.nav{position:absolute;left:0;top:20px;width:1200px;height:47px;background:var(--white)}
.brand{position:absolute;font-weight:800;letter-spacing:1px;color:var(--ink)}
.nav .brand{left:129px;top:8px;font-size:29px;line-height:30px}
.menu{position:absolute;right:129px;top:16px;display:flex;gap:40px;font-size:11.5px;font-weight:600;color:var(--ink);text-transform:uppercase}
.menu .on{color:var(--orange)}

/* hero */
.hero{position:absolute;left:0;top:67px;width:1200px;height:432px;background:linear-gradient(100deg,#2b2d33 0%,#3a3c42 35%,#26282d 70%,#1c1d21 100%)}
.hero h1{position:absolute;left:129px;top:72px;color:var(--white);font-weight:600;font-size:40px;line-height:46px}
.hero h1 small{display:block;font-size:28px;font-weight:400;line-height:36px}
.hero h1 b{font-weight:800;display:block}
.hero p{position:absolute;left:129px;top:213px;width:360px;color:var(--white);font-size:13px;line-height:18px}
.hero-visual{position:absolute;left:636px;top:61px;width:435px;height:330px;background:linear-gradient(135deg,#e0935a 0%,#a55a2c 50%,#4a3428 100%)}
.hero .dots{position:absolute;left:588px;top:395px;display:flex;gap:4px}
.hero .dots i{width:5px;height:5px;background:var(--white)}
.hero .dots i:first-child{background:var(--orange)}

/* section titles */
.kicker{position:absolute;left:0;width:1200px;text-align:center;font-size:17px;font-weight:400}
.title{position:absolute;left:0;width:1200px;text-align:center;font-size:37px;font-weight:700;text-transform:uppercase;line-height:42px}
.title .accent{font-weight:800}
.dark{color:var(--white)}

/* welcome */
.welcome-photo{position:absolute;left:129px;top:570px;width:461px;height:336px;background:linear-gradient(135deg,#c7ccd2,#8e99a6 45%,#3f4c5f);clip-path:polygon(0 2%,100% 12%,100% 88%,0 100%);border-radius:8px}
.welcome-text{position:absolute;left:689px;top:604px;width:382px}
.welcome-text .lead{font-size:17px}
.welcome-text .brand{position:static;font-size:36px;line-height:42px;margin-top:2px}
.welcome-text p{font-size:12.5px;line-height:20px;margin-top:16px;color:var(--ink)}

/* services */
.services{position:absolute;left:0;top:975px;width:1200px;height:481px;background:var(--navy)}
.svc{position:absolute;top:180px;width:274px;height:227px;background:var(--card);color:var(--white)}
.svc h3{position:absolute;left:53px;top:26px;width:210px;font-size:20px;font-weight:600;line-height:25px}
.svc p{position:absolute;left:53px;top:92px;width:200px;font-size:12px;line-height:18.5px;color:#d9dce1}
.svc a{position:absolute;left:53px;top:184px;font-size:12px;color:var(--orange)}
.svc .num{position:absolute;left:-26px;top:40px;font-size:120px;font-weight:800;line-height:110px;color:#a5582a}

/* products */
.product{position:absolute;top:1610px;width:300px;text-align:center}
.laptop{position:relative;width:300px;height:176px}
.laptop .lid{position:absolute;left:27px;top:0;width:246px;height:162px;background:#1d1f23;border-radius:7px 7px 0 0}
.laptop .screen{position:absolute;left:35px;top:8px;width:230px;height:149px}
.laptop .base{position:absolute;left:0;top:162px;width:300px;height:8px;background:linear-gradient(#d9dbde,#a7aaaf);border-radius:0 0 10px 10px}
.product h4{font-size:17px;font-weight:600;margin-top:25px}
.product p{font-size:12.5px;line-height:18px;color:var(--muted);margin:10px auto 0;width:255px}
.product .btn{position:relative;margin:18px auto 0;width:100px;height:34px}

/* news */
.news{position:absolute;left:0;top:1986px;width:1200px;height:503px;background:linear-gradient(180deg,#2a3140,#222a37)}
.post{position:absolute;top:130px;width:300px;color:var(--white)}
.post .ph{width:300px;height:195px}
.post .date{font-size:12px;margin-top:12px}
.post h5{font-size:18.5px;font-weight:500;line-height:22px;margin-top:10px}
.post .btn{position:relative;margin-top:16px;width:100px;height:33px}

/* team */
.member{position:absolute;top:2640px;width:220px;text-align:center}
.member .ph{width:220px;height:240px}
.member h6{font-size:16px;font-weight:600;margin-top:14px;color:var(--ink)}
.member span{font-size:11.5px;color:var(--muted)}

/* quick contact */
.quick-contact{position:absolute;left:0;top:2998px;width:1200px;height:400px;background:linear-gradient(180deg,#29303d,#222834)}
.field{position:absolute;background:var(--white);font-size:12.5px;color:var(--ink);padding:15px 15px}
.submit{position:absolute;left:604px;top:282px;width:387px;height:50px;background:var(--orange);color:var(--white);font-size:12.5px;font-weight:600;display:flex;align-items:center;justify-content:center}

/* footer */
.footer{position:absolute;left:0;top:3398px;width:1200px;height:350px;background:var(--navy-deep);color:var(--white)}
.footer .brand{left:129px;top:42px;font-size:46px;line-height:50px;color:var(--white);letter-spacing:2px}
.footer .about{position:absolute;left:129px;top:118px;width:240px;font-size:12px;line-height:18px}
.footer .sq{position:absolute;top:189px;width:31px;height:31px;background:var(--orange)}
.footer .sq.blue{background:#2b5cd6}
.col{position:absolute;top:58px}
.col h5{color:var(--orange);font-size:16px;font-weight:600}
.col ul{list-style:none;margin-top:6px}
.col li{font-size:11px;line-height:26.5px}
.col li::before{content:"› ";color:var(--orange)}
.info{display:flex;gap:10px;align-items:flex-start;font-size:11.5px;line-height:17px;margin-top:14px}
.info .ic{flex:none;width:27px;height:27px;border-radius:50%;background:var(--orange);display:flex;align-items:center;justify-content:center}
.copy{position:absolute;left:0;top:290px;width:1200px;text-align:center;font-size:11px}
</style>
</head>
<body>

<div class="topbar">
  <i class="soc" style="left:131px"></i>
  <i class="soc" style="left:156px"></i>
  <i class="soc" style="left:187px"></i>
  <div class="topbar-contact">
    <span><svg width="10" height="10" viewBox="0 0 24 24"><path fill="#f47920" d="M6.6 10.8a15 15 0 0 0 6.6 6.6l2.2-2.2a1 1 0 0 1 1-.25 11.4 11.4 0 0 0 3.6.57 1 1 0 0 1 1 1V20a1 1 0 0 1-1 1A17 17 0 0 1 3 4a1 1 0 0 1 1-1h3.5a1 1 0 0 1 1 1c0 1.25.2 2.45.57 3.57a1 1 0 0 1-.25 1z"/></svg>+10 (0) 200 4400</span>
    <span><svg width="11" height="9" viewBox="0 0 22 16"><rect width="22" height="16" rx="2" fill="#f47920"/><path d="M1 2l10 7 10-7" stroke="#1f2530" stroke-width="2" fill="none"/></svg>info@velora.example</span>
  </div>
</div>

<header class="nav">
  <div class="brand">VELORA</div>
  <nav class="menu">
    <span class="on">Home</span><span>Services</span><span>Products</span><span>News</span><span>Team</span><span>Contact Us</span>
  </nav>
</header>

<section class="hero" role="img" aria-label="Dimmed photo of a business team meeting">
  <h1><small>Organize</small><b class="accent">YOUR PROJECTS</b><b>EASIER THAN BEFORE</b></h1>
  <p>Nam libero tempore, cum soluta nobis est eligendi optio cumque nihil impedit</p>
  <div class="btn" style="left:129px;top:276px;width:100px;height:32px">Read More</div>
  <div class="hero-visual" role="img" aria-label="Orange-toned photo collage of smiling professionals"></div>
  <div class="dots"><i></i><i></i><i></i></div>
</section>

<section>
  <div class="welcome-photo" role="img" aria-label="Photo of colleagues discussing around a laptop"></div>
  <div class="welcome-text">
    <div class="lead">Welcome To</div>
    <div class="brand">VELORA</div>
    <p>Sed ut perspiciatis unde omnis iste natus error sit voluptatem accusantium doloremque laudantium, totam rem aperiam, eaque ipsa quae ab illo inventore veritatis et quasi architecto beatae vitae dicta sunt explicabo. Nemo enim ipsam voluptatem quia voluptas sit aspernatur aut odit aut fugit, sed quia consequuntur magni dolores eos qui ratione voluptatem sequi nesciunt.</p>
  </div>
  <div class="btn" style="left:689px;top:858px;width:101px;height:32px">Read More</div>
</section>

<section class="services">
  <div class="kicker dark" style="top:90px">How we do</div>
  <div class="title dark" style="top:112px"><span class="accent">Our</span> Services</div>
  <div class="svc" style="left:156px"><div class="num">1</div><h3>Efficient Database Security</h3><p>Duis aute irure dolor in volup- tate velit esse dolore eu fugiat duis aute irure dolor in volup- tate velit esse dolore</p><a>Read More</a></div>
  <div class="svc" style="left:477px"><div class="num">2</div><h3>Achieve Global Development</h3><p>Duis aute irure dolor in volup- tate velit esse dolore eu fugiat duis aute irure dolor in volup- tate velit esse dolore</p><a>Read More</a></div>
  <div class="svc" style="left:797px"><div class="num">3</div><h3>Analytical Solutions System</h3><p>Duis aute irure dolor in volup- tate velit esse dolore eu fugiat duis aute irure dolor in volup- tate velit esse dolore</p><a>Read More</a></div>
</section>

<section>
  <div class="kicker" style="top:1522px">Featured</div>
  <div class="title" style="top:1544px"><span class="accent">Several</span> Products</div>
  <div class="product" style="left:129px">
    <div class="laptop"><div class="lid"></div><div class="screen" role="img" aria-label="Dashboard screen of the healthcare planning app" style="background:linear-gradient(90deg,#4b4aa8 0 16%,#f3f4f8 16%)"></div><div class="base"></div></div>
    <h4>Healthcare Organizations</h4><p>Sed ut perspiciatis unde omnis iste natus error sit voluptatem</p><div class="btn">Read More</div>
  </div>
  <div class="product" style="left:450px">
    <div class="laptop"><div class="lid"></div><div class="screen" role="img" aria-label="Dashboard screen of the sport club booking app" style="background:linear-gradient(90deg,#e8475a 0 7%,#f4f5f8 7%)"></div><div class="base"></div></div>
    <h4>Sport Clubs</h4><p>Sed ut perspiciatis unde omnis iste natus error sit voluptatem</p><div class="btn">Read More</div>
  </div>
  <div class="product" style="left:771px">
    <div class="laptop"><div class="lid"></div><div class="screen" role="img" aria-label="Dashboard screen of the sports hunting competition app" style="background:linear-gradient(90deg,#1c1c1e 0 6%,#f3f1ec 6%)"></div><div class="base"></div></div>
    <h4>Sports Hunting</h4><p>Sed ut perspiciatis unde omnis iste natus error sit voluptatem</p><div class="btn">Read More</div>
  </div>
</section>

<section class="news">
  <div class="kicker dark" style="top:48px">Recent Post</div>
  <div class="title dark" style="top:70px"><span class="accent">Latest</span> News</div>
  <article class="post" style="left:129px"><div class="ph" role="img" aria-label="Photo of a businesswoman in a glass office" style="background:linear-gradient(135deg,#dfe5ea,#8c98a6)"></div><div class="date"><span class="accent">12th March,</span> 2022</div><h5>At vero eos et accusamus et iusto odio dignissimos</h5><div class="btn">Read More</div></article>
  <article class="post" style="left:449px"><div class="ph" role="img" aria-label="Photo of three colleagues looking at a tablet" style="background:linear-gradient(135deg,#6f5a46,#c9a47c)"></div><div class="date"><span class="accent">12th March,</span> 2022</div><h5>At vero eos et accusamus et iusto odio dignissimos</h5><div class="btn">Read More</div></article>
  <article class="post" style="left:769px"><div class="ph" role="img" aria-label="Photo of two colleagues with a tablet outdoors" style="background:linear-gradient(135deg,#3c587a,#a9a29a)"></div><div class="date"><span class="accent">12th March,</span> 2022</div><h5>At vero eos et accusamus et iusto odio dignissimos</h5><div class="btn">Read More</div></article>
</section>

<section>
  <div class="kicker" style="top:2555px">Members</div>
  <div class="title" style="top:2577px"><span class="accent">Our</span> Team</div>
  <div class="member" style="left:129px"><div class="ph" role="img" aria-label="Portrait of a founder in a suit" style="background:linear-gradient(135deg,#8a6a52,#2d2f36)"></div><h6>Marten Holloway</h6><span>Founder</span></div>
  <div class="member" style="left:369px"><div class="ph" role="img" aria-label="Portrait of a founder in a suit" style="background:linear-gradient(135deg,#cfd2d4,#3a3e46)"></div><h6>Idris Kellan</h6><span>Founder</span></div>
  <div class="member" style="left:609px"><div class="ph" role="img" aria-label="Portrait of an employee" style="background:linear-gradient(135deg,#dedcd9,#8a6a5a)"></div><h6>Lena Varga</h6><span>Employee</span></div>
  <div class="member" style="left:849px"><div class="ph" role="img" aria-label="Portrait of an employee" style="background:linear-gradient(135deg,#c8742c,#2a2a2e)"></div><h6>Tomas Reyvel</h6><span>Employee</span></div>
</section>

<section class="quick-contact">
  <div class="kicker dark" style="top:64px">Contacts</div>
  <div class="title dark" style="top:86px"><span class="accent">Quick</span> Contact</div>
  <div class="field" style="left:208px;top:164px;width:387px;height:50px">Name:</div>
  <div class="field" style="left:208px;top:223px;width:387px;height:50px">Email:</div>
  <div class="field" style="left:208px;top:282px;width:387px;height:50px">Phone:</div>
  <div class="field" style="left:604px;top:164px;width:387px;height:109px">Message:</div>
  <div class="submit">SUBMIT</div>
</section>

<footer class="footer">
  <div class="brand">VELORA</div>
  <p class="about">At vero eos et accusamus et iusto odio dignissimos ducimus qui blanditiis praesentium</p>
  <i class="sq blue" style="left:129px"></i><i class="sq" style="left:166px"></i><i class="sq" style="left:202px"></i>
  <div class="col" style="left:442px"><h5>Sitemap</h5><ul><li>Home</li><li>Services</li><li>Products</li><li>News</li><li>Team</li><li>Contact Us</li></ul></div>
  <div class="col" style="left:615px"><h5>Products</h5><ul><li>Healthcare Organizations</li><li>Sport Clubs</li><li>Sports Hunting</li></ul></div>
  <div class="col" style="left:849px;width:230px"><h5>Contact Us</h5>
    <div class="info"><span class="ic"><svg width="11" height="14" viewBox="0 0 12 16"><path fill="#fff" d="M6 0a6 6 0 0 0-6 6c0 4.5 6 10 6 10s6-5.5 6-10a6 6 0 0 0-6-6zm0 8.2A2.2 2.2 0 1 1 6 3.8a2.2 2.2 0 0 1 0 4.4z"/></svg></span><span>22/B Lorem ipsum dolor sit amet Northfield 40K USA</span></div>
    <div class="info"><span class="ic"><svg width="12" height="12" viewBox="0 0 24 24"><path fill="#fff" d="M6.6 10.8a15 15 0 0 0 6.6 6.6l2.2-2.2a1 1 0 0 1 1-.25 11.4 11.4 0 0 0 3.6.57 1 1 0 0 1 1 1V20a1 1 0 0 1-1 1A17 17 0 0 1 3 4a1 1 0 0 1 1-1h3.5a1 1 0 0 1 1 1c0 1.25.2 2.45.57 3.57a1 1 0 0 1-.25 1z"/></svg></span><span style="padding-top:5px">+10 (0) 200 4400</span></div>
    <div class="info"><span class="ic"><svg width="13" height="10" viewBox="0 0 22 16"><rect width="22" height="16" rx="2" fill="#fff"/><path d="M1 2l10 7 10-7" stroke="#f47920" stroke-width="2" fill="none"/></svg></span><span style="padding-top:5px">info@velora.example</span></div>
  </div>
  <div class="copy">Copyright © 2022 <span class="accent">Velora</span>. All Rights Reserved.</div>
</footer>

</body>
</html>
```